graphic showing our process of education as a process called a pipeline

Also see my updated comments on discussion section.
Title of the graphic needs to be:
TITLE = The KESIMA Strategic Leadership Pipeline = larger, bold heading
SUB-TITLE = Developing a steady flow of servant leaders for Tanzania's future = under title; smaller font
change the text for each of the 7 steps to match the outcomes listed on the newly attached PDF (strategic pipeline 11x17)
Pipe should be straight or mostly straight.
Pipe should not be in a strong or dark color.
Any icons or symbols should be simple and professional, not like cartoon or childish.
We need a graphic design that shows our PROCESS, called a "pipeline," that is creating future leaders. We are a US-based non-profit that operates a Christian school in rural Tanzania for 600 students (pre-K through 12th grade). It starts with child sponsorship program that allows poor children and orphans to attend school, we have a primary school (like USA elementary school, pre-K thru 7th), and are building a secondary boarding school (like USA middle and high school, grades 8-12), where students will live on campus in dormitories. We offer education, scholarships, leadership development experiences, help finding and securing college scholarships, academic and career counseling, placements for internships and jobs, and networking and leadership development content and events to create the next generation of servant leaders for the country. Prominent colors should probably be the green, blue and black in the Tanzania flag; we want the design to communicate "smart" and "strategic." The stages of the pipeline need to be properly named; we need to show a "leak" in the pipeline after the primary school because we currently have to send our students AWAY to other boarding schools because we don't have one. As the attached recording says, this is bad for their progress. The attached pipeline graphic is very rough and NOT meant to be imitated. It is factually correct, but is busy and not attractive.

Target Market(s)

Major financial contributors and foundations that want to give money to the cause

Industry/Entity Type

non-profit/Christian ministry in education

Font styles to use
Sans Serif

Requirements
Must have
• A "smart" and strategic" feel; preferably visible when on a half page
Nice to have
• a smart, sophisticated, serious look and feel
Should not have
• an elementary school feel

```html
<!DOCTYPE html>
<html lang="en">
<head>
<meta charset="utf-8">
<title>The KESIMA Strategic Leadership Pipeline</title>
<link href="https://fonts.googleapis.com/css2?family=Montserrat:wght@500;600;700;800&display=swap" rel="stylesheet">
<style>
  :root {
    --brand-blue: #1b9ad6;
    --stage-blue: #1f9bd5;
    --icon-green: #2bb24c;
    --panel-tint: #e4f4fb;
    --pipe-grey: #d8d8d8;
    --ink: #111111;
    --white: #ffffff;
  }
  * { margin: 0; padding: 0; box-sizing: border-box; }
  html, body {
    width: 1200px; height: 1200px; overflow: hidden;
    background: var(--white);
    font-family: "Montserrat", Arial, sans-serif;
    color: var(--ink);
  }
  .canvas { position: relative; width: 1200px; height: 1200px; }

  .headline {
    position: absolute; top: 214px; left: 0; width: 1200px;
    text-align: center; font-size: 40px; font-weight: 800; line-height: 1.2;
    color: var(--brand-blue); white-space: nowrap;
  }
  .subtitle {
    position: absolute; top: 280px; left: 60px; width: 1080px;
    text-align: center; font-size: 21px; font-weight: 500; line-height: 1.25;
  }
  .tagline {
    position: absolute; top: 318px; left: 60px; width: 1080px;
    text-align: center; font-size: 19px; font-weight: 800; line-height: 1.25;
  }

  .pipeline-panel {
    position: absolute; left: 97px; top: 365px; width: 1037px; height: 426px;
    background: var(--panel-tint);
  }

  .stage { position: absolute; top: 380px; width: 142px; margin-left: -71px; text-align: center; }
  .stage-label {
    margin: 0 auto; width: 116px; height: 74px;
    background: var(--stage-blue); color: var(--white);
    font-size: 11.5px; font-weight: 700; line-height: 1.15;
    display: flex; align-items: flex-start; justify-content: center;
    padding-top: 11px;
  }
  .stage-icon {
    margin: 16px auto 0; width: 46px; height: 46px;
    background: var(--icon-green); border-radius: 6px;
  }
  .stage-drop {
    margin: 16px auto 0; width: 0; height: 66px;
    border-left: 3px dotted var(--stage-blue);
  }
  .stage-outcome {
    position: absolute; top: 678px; width: 120px; margin-left: -60px;
    text-align: center; font-size: 9.4px; font-weight: 500; line-height: 1.13;
  }

  .pipe { position: absolute; left: 0; top: 0; }
</style>
</head>
<body>
<main class="canvas">
  <h1 class="headline">The KESIMA Strategic Leadership Pipeline</h1>
  <p class="subtitle">Developing a steady flow of servant leaders for Tanzania’s future</p>
  <p class="tagline">KESIMA’s pipeline is ending this cycle!</p>

  <section class="pipeline-panel"></section>

  <svg class="pipe" width="1200" height="1200" viewBox="0 0 1200 1200" aria-hidden="true">
    <rect x="234" y="605" width="876" height="30" fill="var(--pipe-grey)"/>
    <g fill="var(--stage-blue)">
      <rect x="230" y="600" width="3" height="40"/><rect x="236" y="600" width="3" height="40"/>
      <rect x="518" y="600" width="3" height="40"/><rect x="524" y="600" width="3" height="40"/>
      <rect x="808" y="600" width="3" height="40"/><rect x="814" y="600" width="3" height="40"/>
      <rect x="1104" y="600" width="3" height="40"/><rect x="1110" y="600" width="3" height="40"/>
    </g>
    <line x1="171" y1="582" x2="212" y2="614" stroke="var(--stage-blue)" stroke-width="3" stroke-dasharray="3 4"/>
    <polygon points="218,620 204,618 212,607" fill="var(--stage-blue)"/>
    <polygon points="384,606 372,626 381,626 374,642 392,618 383,618 390,606" fill="var(--stage-blue)"/>
    <path d="M387 648 C387 648 376 662 376 670 a11 11 0 0 0 22 0 C398 662 387 648 387 648 Z" fill="none" stroke="var(--stage-blue)" stroke-width="2.5"/>
    <path d="M387 656 C387 656 380 665 380 670 a7 7 0 0 0 7 7 Z" fill="var(--stage-blue)"/>
  </svg>

  <div class="stage" style="left:171px">
    <div class="stage-label">KESIMA<br>Sponsorship<br>Project</div>
    <div class="stage-icon" role="img" aria-label="Icon of a child"></div>
    <div class="stage-drop" style="height:52px"></div>
  </div>
  <div class="stage" style="left:314px">
    <div class="stage-label">KESIMA<br>Leadership<br>Primary<br>School</div>
    <div class="stage-icon" role="img" aria-label="Icon of a teacher with a pupil"></div>
    <div class="stage-drop"></div>
  </div>
  <div class="stage" style="left:455px">
    <div class="stage-label">KESIMA<br>Leadership<br>Secondary<br>School</div>
    <div class="stage-icon" role="img" aria-label="Icon of a student with a science atom"></div>
    <div class="stage-drop"></div>
  </div>
  <div class="stage" style="left:598px">
    <div class="stage-label">KESIMA<br>Service<br>Leadership<br>Experience</div>
    <div class="stage-icon" role="img" aria-label="Icon of a person helping another up"></div>
    <div class="stage-drop"></div>
  </div>
  <div class="stage" style="left:740px">
    <div class="stage-label">KESIMA<br>Higher<br>Education<br>Support</div>
    <div class="stage-icon" role="img" aria-label="Icon of a graduate in a cap"></div>
    <div class="stage-drop"></div>
  </div>
  <div class="stage" style="left:881px">
    <div class="stage-label">KESIMA<br>Employment<br>Center</div>
    <div class="stage-icon" role="img" aria-label="Icon of a person walking with a briefcase"></div>
    <div class="stage-drop"></div>
  </div>
  <div class="stage" style="left:1024px">
    <div class="stage-label">KESIMA<br>Leadership<br>Hub</div>
    <div class="stage-icon" role="img" aria-label="Icon of a leader among a group"></div>
    <div class="stage-drop"></div>
  </div>

  <p class="stage-outcome" style="left:171px">Identifies children who can thrive from among the poor and pairs them with sponsors to provide a quality education.</p>
  <p class="stage-outcome" style="left:314px">Provides excellence in education, emphasizing problem-solving, creativity, and a Biblical worldview to prepare future servant leaders.</p>
  <p class="stage-outcome" style="left:455px">(In progress)<br>Will focus on advanced education, including STEM subjects, for top students from across Tanzania, fostering innovation and leadership.</p>
  <p class="stage-outcome" style="left:598px">Engages graduates in hands-on volunteer projects that transform them into servant leaders as they solve urgent community problems.</p>
  <p class="stage-outcome" style="left:740px">Guides students through the application process, and provides scholarships and mentorship to obtain an education that would otherwise be out of reach.</p>
  <p class="stage-outcome" style="left:881px">Facilitates job placements through internships and a startup incubator to help graduates secure high-impact careers.</p>
  <p class="stage-outcome" style="left:1024px">Provides ongoing leadership training and networking opportunities, and positions graduates in roles that influence local and national transformation.</p>
</main>
</body>
</html>
```